Steadfast Corner Vending Needs a Promotional Flyer

Design a one page, one sided 8 1/2" x 11" flyer that can be handed out to potential customers. Please keep printing efficiencies in mind. See attached old flyers and company website (steadfastcornervend.example) for reference of services. I have also attached our current logo.

```html
<!DOCTYPE html>
<html lang="en">
<head>
<meta charset="utf-8">
<title>Steadfast Corner Vending – Flyer</title>
<link href="https://fonts.googleapis.com/css2?family=Poppins:wght@300;400;500;600;700;800&display=swap" rel="stylesheet">
<style>
:root{
  --navy:#13364a;
  --navy-deep:#0f2c3d;
  --blue:#3bb0e6;
  --blue-soft:#6cc6ee;
  --white:#ffffff;
  --ink:#1c2b36;
}
*{margin:0;padding:0;box-sizing:border-box}
html,body{width:783px;height:1200px;overflow:hidden;background:#fff}
body{font-family:"Poppins",Arial,sans-serif;color:var(--ink)}
.flyer{position:relative;width:783px;height:1200px;overflow:hidden;background:var(--white)}
.abs{position:absolute}
.backdrop{position:absolute;left:0;top:0}

.brand{left:50px;top:78px;display:flex;align-items:center;gap:10px}
.brand-mark{width:26px;height:26px;background:var(--blue)}
.brand-name{font-weight:700;font-size:19px;color:var(--navy);line-height:1.1}

.welcome{left:46px;top:176px;font-weight:300;font-size:36px;letter-spacing:7px;color:var(--navy);line-height:1}
.headline{left:44px;top:214px;font-weight:800;line-height:.98;letter-spacing:-1px}
.headline .dark{display:block;font-size:54px;color:var(--navy)}
.headline .light{display:block;font-size:70px;color:var(--blue)}

.machine-photo{left:405px;top:52px;width:300px;height:440px;border-radius:4px;
  background:linear-gradient(90deg,#d9412a 0%,#e55232 45%,#2a2d31 50%,#3a3f45 100%)}

.tab{height:30px;background:var(--blue);color:var(--white);font-weight:700;font-size:13px;
  display:flex;align-items:center;padding-left:14px;text-transform:uppercase;white-space:nowrap;
  clip-path:polygon(0 0,92% 0,100% 100%,0 100%)}
.tab b{color:var(--navy);font-weight:700;margin-left:4px}
.tab b.joined{margin-left:0}
.tab-why{left:44px;top:434px;width:300px;font-size:13.5px}

.why-list{list-style:none;color:var(--white);font-size:11px;line-height:1.2;width:250px}
.why-list li{position:relative;padding-left:12px;margin-bottom:15px}
.why-list li::before,.list li::before{content:"";position:absolute;left:0;top:4px;width:5px;height:5px;border:1.5px solid var(--blue);border-radius:50%}
.why-left{left:50px;top:496px}
.why-right{left:326px;top:496px;width:290px}
.why-right li{margin-bottom:9px}

.list{list-style:none;font-size:10.5px;font-weight:500;line-height:1.15;color:var(--ink)}
.list li{position:relative;padding-left:11px}
.list.spaced li{margin-bottom:17px}
.photo{border:3px solid #fff;box-shadow:0 1px 5px rgba(0,0,0,.25)}

.intro{font-size:10.5px;line-height:1.2;color:var(--ink)}
.intro .accent{color:var(--blue);font-weight:500}
.intro strong{font-weight:700;display:block;margin-top:4px}
.sub-title{font-weight:700;font-size:13px;color:var(--navy)}

.footer-text{color:var(--white);font-weight:500;display:flex;align-items:center;gap:6px;white-space:nowrap}
.footer-phone{left:44px;top:1124px;font-size:17px}
.footer-web{left:210px;top:1126px;font-size:14px}
.address{left:486px;top:1118px;font-size:12.5px;font-weight:600;color:var(--navy);line-height:1.25;display:flex;gap:6px;width:290px}
</style>
</head>
<body>
<main class="flyer">

  <svg class="backdrop" width="783" height="1200" viewBox="0 0 783 1200" aria-hidden="true">
    <polygon points="520,0 783,0 783,610 700,623 430,623" fill="#2f8fc4"/>
    <polygon points="560,0 640,0 470,120 430,95" fill="#13364a"/>
    <polygon points="0,449 440,449 640,623 0,623" fill="#13364a"/>
    <polygon points="640,623 783,560 783,623" fill="#13364a"/>
    <rect x="0" y="1089" width="783" height="111" fill="#13364a"/>
    <polygon points="436,1089 783,1089 783,1182 501,1182" fill="#ffffff"/>
  </svg>

  <div class="abs brand">
    <span class="brand-mark"></span>
    <span class="brand-name">Steadfast Corner Vending</span>
  </div>

  <div class="abs welcome">WELCOME TO</div>
  <h1 class="abs headline">
    <span class="dark">STEADFAST</span>
    <span class="light">CORNER</span>
    <span class="light">VENDING</span>
  </h1>

  <div class="abs machine-photo" role="img" aria-label="Photo of a red drinks vending machine beside a black snack vending machine"></div>

  <div class="abs tab tab-why">Why choose Steadfast Corner?</div>
  <ul class="abs why-list why-left">
    <li>Our warehouse is just minutes away so we can get there quickly if a problem should arise.</li>
    <li>We are a small company that is BIG on service.</li>
    <li>We are Owner-Operators so we truly CARE about our customers.</li>
  </ul>
  <ul class="abs why-list why-right">
    <li>We are also trained to fix many problems on the spot.</li>
    <li>We will supply machines to your facility.</li>
    <li>Customer Service is our priority.</li>
    <li>Your employees can choose what types of snacks and drinks they would like to see in the machines.</li>
  </ul>

  <!-- Vending machine services -->
  <div class="abs tab" style="left:44px;top:648px;width:218px">Vending<b>Machine Services</b></div>
  <div class="abs intro" style="left:44px;top:690px;width:220px">
    Discover Reliability, Convenience, Quality, and Variety<br>
    <span class="accent">At Zero Cost to You</span>
    <strong>Why Choose Our Vending Machine Services?</strong>
  </div>
  <ul class="abs list" style="left:44px;top:768px">
    <li>Zero Cost to you</li><li>Reliability</li><li>Convenience</li><li>Quality</li>
  </ul>
  <ul class="abs list" style="left:147px;top:768px">
    <li>Variety</li><li>Customization</li><li>Technology</li><li>On-time Maintenance</li>
  </ul>
  <div class="abs photo" role="img" aria-label="Photo of a colourful vending machine in a shop" style="left:279px;top:681px;width:112px;height:157px;background:linear-gradient(160deg,#2f4b5e,#c86a2c 55%,#1f2c35)"></div>

  <!-- Coffee service -->
  <div class="abs tab" style="left:418px;top:648px;width:183px">Coffee<b>Service</b></div>
  <div class="abs sub-title" style="left:418px;top:691px">Our Coffee Selection</div>
  <ul class="abs list spaced" style="left:418px;top:722px">
    <li>Harbor Roast</li><li>Morning Ring</li><li>Polar Bean</li><li>Antler Brew</li>
  </ul>
  <ul class="abs list" style="left:526px;top:722px">
    <li style="margin-bottom:15px">Stillwater</li>
    <li style="margin-bottom:10px">Fieldgrain</li>
    <li>Hearthstone<br>and other<br>specialty brands<br>upon request</li>
  </ul>
  <div class="abs photo" role="img" aria-label="Photo of a coffee grinder filled with beans" style="left:640px;top:681px;width:114px;height:157px;background:linear-gradient(150deg,#8a8f93,#3a2a22 55%,#d8d8d8)"></div>

  <!-- Pantry service -->
  <div class="abs tab" style="left:44px;top:870px;width:218px">Pantry<b>Service</b></div>
  <ul class="abs list" style="left:44px;top:915px;width:100px">
    <li style="margin-bottom:14px">A Snack Time Oasis in Your Workspace</li>
    <li style="margin-bottom:14px">Tailored to Your Tastes</li>
    <li>Healthy Choices, Happy Teams</li>
  </ul>
  <ul class="abs list" style="left:147px;top:915px;width:115px">
    <li style="margin-bottom:14px">Seamless Restocking and Management</li>
    <li style="margin-bottom:14px">Flexible and Hassle-Free</li>
    <li>Enhancing Workplace Culture</li>
  </ul>
  <div class="abs photo" role="img" aria-label="Photo of a lit snack vending machine against a blue wall" style="left:279px;top:903px;width:112px;height:157px;background:linear-gradient(160deg,#1c3a8a,#b8452c 50%,#152042)"></div>

  <!-- Micro-market -->
  <div class="abs tab" style="left:418px;top:870px;width:183px">Micro-<b class="joined">Market</b></div>
  <ul class="abs list" style="left:418px;top:915px;width:100px">
    <li style="margin-bottom:14px">Experience Unmatched Convenience</li>
    <li style="margin-bottom:14px">Tailored to Your Taste</li>
    <li>Seamless and Secure Transactions</li>
  </ul>
  <ul class="abs list" style="left:526px;top:915px;width:110px">
    <li style="margin-bottom:14px">Freshness Guaranteed</li>
    <li style="margin-bottom:14px">Smart Inventory Management</li>
    <li>Promoting Workplace Wellbeing</li>
  </ul>
  <div class="abs photo" role="img" aria-label="Photo of shoppers at a self-service micro-market cooler" style="left:640px;top:903px;width:114px;height:157px;background:linear-gradient(160deg,#6e6355,#c9c4bb 50%,#3c3a3a)"></div>

  <!-- Footer -->
  <div class="abs footer-text footer-phone">
    <svg width="14" height="14" viewBox="0 0 24 24" aria-hidden="true"><path d="M6.6 10.8a15.1 15.1 0 0 0 6.6 6.6l2.2-2.2c.3-.3.7-.4 1-.2 1.1.4 2.300.6 3.6.6.6 0 1 .4 1 1V20c0 .6-.4 1-1 1A17 17 0 0 1 3 4c0-.6.4-1 1-1h3.5c.6 0 1 .4 1 1 0 1.3.2 2.5.6 3.6.1.3 0 .7-.2 1z" fill="#3bb0e6"/></svg>
    555-014-2290
  </div>
  <div class="abs footer-text footer-web">
    <svg width="13" height="13" viewBox="0 0 24 24" aria-hidden="true" fill="none" stroke="#3bb0e6" stroke-width="2"><circle cx="12" cy="12" r="10"/><path d="M2 12h20M12 2c3 3 3 17 0 20M12 2c-3 3-3 17 0 20"/></svg>
    steadfastcornervend.example
  </div>
  <div class="abs address">
    <svg width="12" height="16" viewBox="0 0 24 32" aria-hidden="true" style="flex:none;margin-top:2px"><path d="M12 0C5.4 0 0 5.4 0 12c0 9 12 20 12 20s12-11 12-20C24 5.4 18.6 0 12 0zm0 17a5 5 0 1 1 0-10 5 5 0 0 1 0 10z" fill="#3bb0e6"/></svg>
    <span>1480 Meridian Ave. Unit 210, Lakemont, Illinois 60000, United States</span>
  </div>

</main>
</body>
</html>
```